Classy, Elegant, Simple Business Card Design

Looking to have a classy, simple, and elegant design. Want a top notch designed business card. I really like the look of the new torvane credit card. I also like the design I attached. I am trying to reach 21-29 year old females for booking us for there wedding or event. We offer Disc Jockey Service, Photo Booth Rentals, and Uplighting .

Target Market(s)

21-28 year old females

Contact Information for Business Card

Has to have logo, website, email, and phone number

Font styles to use
Other font styles liked:
• open to font choice, modern, clean
Designer to choose
33a6d7
0791cd
0555a3
ffffff

Requirements
Must have
• Has to have logo, website, email, and phone number
Nice to have
• I really like the design of the new torvane credit card. I also included my logo and some designs I like
Should not have
• clutter or too much info

```html
<!DOCTYPE html>
<html lang="en">
<head>
<meta charset="utf-8">
<title>Tidehall Event Group – Business Card</title>
<link rel="stylesheet" href="https://fonts.googleapis.com/css2?family=Work+Sans:wght@400;500;600&display=swap">
<style>
  :root{
    --bg:#a9a9a9;
    --navy:#13305a;
    --navy-light:#1d4272;
    --blue:#0791cd;
    --blue-deep:#0555a3;
    --blue-soft:#33a6d7;
    --white:#ffffff;
    --grey-text:#8a8f96;
  }
  *{box-sizing:border-box;margin:0;padding:0}
  html,body{width:1200px;height:930px;overflow:hidden}
  body{
    background:radial-gradient(ellipse at 55% 40%, #c4c4c4 0%, var(--bg) 75%);
    font-family:"Work Sans", sans-serif;
    position:relative;
  }
  .card{
    position:absolute;
    width:540px;height:310px;
    border-radius:22px;
    overflow:hidden;
    box-shadow:0 10px 26px rgba(0,0,0,.28);
  }
  .card--front{
    left:90px;top:120px;
    background:linear-gradient(100deg,var(--navy) 0%,var(--navy-light) 30%,var(--navy) 60%);
    color:var(--white);
    text-align:center;
  }
  .card--back{
    left:570px;top:500px;
    background:linear-gradient(100deg,var(--navy) 0%,var(--navy-light) 40%,var(--navy) 70%);
  }
  .wordmark{
    display:flex;align-items:center;justify-content:center;gap:12px;
    font-weight:600;letter-spacing:3px;font-size:26px;
    color:var(--blue-soft);
  }
  .wordmark__dot{width:14px;height:14px;border-radius:50%;background:var(--blue-soft)}
  .tagline{
    font-size:11px;letter-spacing:7px;color:#b8c4d4;margin-top:8px;text-transform:uppercase;
  }
  .card--front .wordmark{margin-top:112px}
  .card--front .site{
    position:absolute;left:0;right:0;bottom:52px;
    font-size:14px;letter-spacing:2px;color:var(--white);
  }
  .curve{position:absolute;inset:0}
  .card--back .brand{
    position:absolute;right:36px;top:70px;text-align:center;
  }
  .card--back .wordmark{color:var(--blue-deep);font-size:24px}
  .card--back .wordmark__dot{background:var(--blue-deep)}
  .card--back .tagline{color:var(--grey-text)}
  .contact{
    position:absolute;left:34px;bottom:28px;color:var(--white);
    font-size:13px;line-height:1.45;
  }
  .contact__name{font-weight:600;font-size:19px;letter-spacing:.5px;line-height:1.1}
  .contact__role{font-size:13px;margin-bottom:10px}
  .contact__address{margin-bottom:10px}
  .contact__row{display:flex;align-items:center;gap:9px}
  .contact__row svg{width:11px;height:11px;flex:none}
</style>
</head>
<body>

  <section class="card card--front" aria-label="Card front">
    <div class="wordmark"><span class="wordmark__dot"></span>TIDEHALL</div>
    <p class="tagline">Event Group</p>
    <p class="site">www.tidehallevents.com</p>
  </section>

  <section class="card card--back" aria-label="Card back">
    <svg class="curve" viewBox="0 0 540 310" preserveAspectRatio="none" aria-hidden="true">
      <path d="M215 0 Q300 250 540 232 L540 0 Z" fill="var(--white)"/>
      <path d="M215 0 Q300 250 540 232" fill="none" stroke="var(--blue)" stroke-width="6"/>
      <path d="M200 0 Q290 262 540 244" fill="none" stroke="var(--blue-deep)" stroke-width="2" opacity=".7"/>
    </svg>

    <div class="brand">
      <div class="wordmark"><span class="wordmark__dot"></span>TIDEHALL</div>
      <p class="tagline">Event Group</p>
    </div>

    <div class="contact">
      <p class="contact__name">DORIAN VALE</p>
      <p class="contact__role">Managing Partner</p>
      <p class="contact__address">418 Merrow Lane,<br>Fenwick, CA 90117</p>
      <p class="contact__row">
        <svg viewBox="0 0 24 24" aria-hidden="true"><path fill="#fff" d="M6.6 10.8a15 15 0 0 0 6.6 6.6l2.2-2.2c.3-.3.7-.4 1-.2 1.1.4 2.3.6 3.6.6.6 0 1 .4 1 1V20c0 .6-.4 1-1 1A17 17 0 0 1 3 4c0-.6.4-1 1-1h3.5c.6 0 1 .4 1 1 0 1.3.2 2.5.6 3.6.1.3 0 .7-.2 1z"/></svg>
        555-014-2290
      </p>
      <p class="contact__row">
        <svg viewBox="0 0 24 24" aria-hidden="true"><rect x="2" y="5" width="20" height="14" rx="2" fill="none" stroke="#fff" stroke-width="2"/><path d="M2 6l10 7 10-7" fill="none" stroke="#fff" stroke-width="2"/></svg>
        hello@tidehallevents.com
      </p>
      <p class="contact__row">
        <svg viewBox="0 0 24 24" aria-hidden="true"><circle cx="12" cy="12" r="9" fill="none" stroke="#fff" stroke-width="2"/><path d="M3 12h18M12 3c3 3 3 15 0 18M12 3c-3 3-3 15 0 18" fill="none" stroke="#fff" stroke-width="1.6"/></svg>
        www.tidehallevents.com
      </p>
    </div>
  </section>

</body>
</html>
```